Brell Stone Company Business Cards

Front and Back Business Card - logo and text setup - cool design. I need workable photoshop or illustrator files so I can setup each employee card with design that is created
Updates

Hi everyone, thank you for the great entries. Please no more white and blue cards - there are so many already - black and silver only now please. thanks!

Target Market(s)

Construction Industry - Facility Managers

Industry/Entity Type

Construction

Contact Information for Business Card

I really like contemporary simplistic looks - clean neat....not opposed to seeing some black backrounds

Requirements
Must have
• Logo/website address with design on front only - www.brellstone-example.com (logo attached)
• Back:
• Name/Title/Company Address/Phone/email address
Nice to have
• Cool design
Should not have
• Nothing gimmicky like Fire or Water - since we are a Fire Protection company - it has all been done

```html
<!DOCTYPE html>
<html lang="en">
<head>
<meta charset="utf-8">
<title>Brell Stone Company Business Cards</title>
<link href="https://fonts.googleapis.com/css2?family=Work+Sans:wght@400;500;700&display=swap" rel="stylesheet">
<style>
  :root {
    --backdrop: #3a3532;
    --card: #151516;
    --silver: #c4c7cc;
    --silver-bright: #e6e8eb;
    --silver-dark: #8c9096;
    --text-light: #e9eaec;
    --icon-grey: #9a9ea5;
  }
  * { margin: 0; padding: 0; box-sizing: border-box; }
  html, body { width: 1200px; height: 715px; overflow: hidden; }
  body {
    background: var(--backdrop);
    font-family: "Work Sans", sans-serif;
    position: relative;
  }
  .card {
    position: absolute;
    top: 203px;
    width: 540px;
    height: 309px;
    background: var(--card);
    border-radius: 3px;
    overflow: hidden;
    box-shadow: 0 10px 30px rgba(0,0,0,.45);
  }
  .card--front { left: 40px; }
  .card--back { left: 620px; }

  .brand {
    display: flex;
    align-items: center;
    gap: 10px;
    color: var(--silver);
    font-weight: 700;
    letter-spacing: .5px;
  }
  .brand__square {
    width: 14px; height: 14px;
    background: var(--silver-bright);
  }
  .card--front .brand {
    position: absolute;
    left: 0; right: 0; top: 118px;
    justify-content: center;
    font-size: 44px;
  }
  .card--front .brand__square { width: 26px; height: 26px; }
  .front-website {
    position: absolute;
    left: 0; right: 0; top: 190px;
    text-align: center;
    color: var(--silver-dark);
    font-size: 15px;
    letter-spacing: 1.5px;
  }
  .front-edge {
    position: absolute;
    left: 0; right: 0; bottom: 0;
    height: 10px;
    background: var(--silver-dark);
  }

  .card--back .brand {
    position: absolute;
    left: 38px; top: 34px;
    font-size: 30px;
  }
  .divider {
    position: absolute;
    left: 38px; right: 38px; top: 140px;
    height: 1.5px;
    background: var(--silver);
  }
  .person {
    position: absolute;
    right: 38px; top: 88px;
    text-align: right;
  }
  .person__name {
    color: var(--silver-bright);
    font-size: 22px;
    font-weight: 500;
    letter-spacing: 1px;
    text-transform: uppercase;
  }
  .person__title {
    color: var(--silver-dark);
    font-size: 14px;
    margin-top: 3px;
  }
  .contacts {
    position: absolute;
    left: 38px; top: 160px;
    list-style: none;
    color: var(--text-light);
    font-size: 14px;
    line-height: 24px;
  }
  .contacts li { display: flex; align-items: center; gap: 10px; }
  .contacts svg { width: 11px; height: 11px; fill: var(--icon-grey); }
  .address {
    position: absolute;
    right: 38px; top: 226px;
    text-align: right;
    color: var(--text-light);
    font-size: 15px;
    line-height: 22px;
  }
  .edge-line {
    position: absolute;
    left: 0; right: 0; bottom: 12px;
    height: 2px;
    background: var(--silver-bright);
  }
  .edge-band {
    position: absolute;
    left: 0; right: 0; bottom: 0;
    height: 10px;
    background: var(--silver-dark);
  }
</style>
</head>
<body>

  <section class="card card--front" aria-label="Card front">
    <div class="brand"><span class="brand__square"></span>Brell Stone</div>
    <div class="front-website">www.brellstone-example.com</div>
    <div class="front-edge"></div>
  </section>

  <section class="card card--back" aria-label="Card back">
    <div class="brand"><span class="brand__square"></span>Brell Stone</div>

    <div class="person">
      <div class="person__name">Dorian Hale</div>
      <div class="person__title">Director</div>
    </div>

    <div class="divider"></div>

    <ul class="contacts">
      <li><svg viewBox="0 0 12 12"><path d="M2 0h3l1 3-2 1.5a7 7 0 0 0 3.5 3.5L9 6l3 1v3c0 1-1 2-2 2A10 10 0 0 1 0 2c0-1 1-2 2-2z"/></svg>(555) 014-2290</li>
      <li><svg viewBox="0 0 12 12"><rect x="3" y="0" width="6" height="12" rx="1.2"/></svg>(555) 014-2291</li>
      <li><svg viewBox="0 0 12 12"><path d="M0 2h12v8H0z M0 2l6 5 6-5" fill="none" stroke="#9a9ea5" stroke-width="1.4"/></svg>info@brellstone-example.com</li>
      <li><svg viewBox="0 0 12 12"><circle cx="6" cy="6" r="6"/></svg>www.brellstone-example.com</li>
    </ul>

    <div class="address">
      48 Quarry Lane<br>
      Marlow Ridge, NY 10990
    </div>

    <div class="edge-line"></div>
    <div class="edge-band"></div>
  </section>

</body>
</html>
```